Business Card Design

We need a business card designed for our new company. Prefer a black card with white logo & writing.

Contact Information for Business Card

Ted Galloway, address: 7-4812 Fernhollow Road, Abbotsford, BC, V3K 8R2, Office Phone: 604-712-3390, Cell: 604-947-2164, Email: ted@resinworkshub.ca

Colors

Designer to choose only greyscale colors for use in the design.

```html
<!DOCTYPE html>
<html lang="en">
<head>
<meta charset="UTF-8">
<title>Resinworks Hub — Business Card</title>
<link href="https://fonts.googleapis.com/css2?family=Poppins:wght@300;400;600;700&display=swap" rel="stylesheet">
<style>
  :root {
    --backdrop: #232325;
    --card: #1c1c1f;
    --card-edge: #3a3a3e;
    --ink: #ffffff;
    --ink-muted: #cfcfd2;
    --mark-front: #5a5a5f;
  }
  * { margin: 0; padding: 0; box-sizing: border-box; }
  html, body {
    width: 1200px; height: 711px; overflow: hidden;
    background: var(--backdrop);
    font-family: "Poppins", sans-serif;
  }
  .stage { position: relative; width: 1200px; height: 711px; }
  .card {
    position: absolute;
    width: 540px; height: 309px;
    top: 201px;
    background: var(--card);
    border: 1px solid var(--card-edge);
    border-radius: 22px;
    overflow: hidden;
  }
  .card--front { left: 40px; }
  .card--back { left: 620px; }

  .brand {
    display: flex; align-items: center; gap: 10px;
    font-weight: 700; letter-spacing: 1px; text-transform: uppercase;
    white-space: nowrap;
  }
  .brand__dot { border-radius: 50%; flex: none; }

  .card--front .brand {
    position: absolute; left: 50%; top: 50%;
    transform: translate(-50%, -50%);
    color: var(--mark-front); font-size: 34px;
  }
  .card--front .brand__dot { width: 22px; height: 22px; background: var(--mark-front); }

  .card--back .brand {
    position: absolute; right: 34px; top: 38px;
    color: var(--ink); font-size: 22px;
  }
  .card--back .brand__dot { width: 14px; height: 14px; background: var(--ink); }

  .address {
    position: absolute; right: 34px; top: 104px;
    text-align: right; color: var(--ink);
    font-size: 12.5px; font-weight: 300; line-height: 1.45;
  }
  .contacts {
    position: absolute; right: 34px; top: 158px;
    list-style: none; color: var(--ink);
    font-size: 12.5px; font-weight: 300;
  }
  .contacts li {
    display: flex; justify-content: flex-end; align-items: center;
    gap: 8px; height: 22px;
  }
  .contacts svg { width: 13px; height: 13px; fill: none; stroke: var(--ink); stroke-width: 1.6; }

  .person {
    position: absolute; left: 28px; bottom: 22px;
    transform-origin: left bottom;
    transform: rotate(-90deg) translate(0, 100%);
    color: var(--ink); white-space: nowrap;
  }
  .person__name { font-size: 28px; line-height: 1.1; }
  .person__first { font-weight: 700; }
  .person__last { font-weight: 300; }
  .person__title { font-size: 11.5px; font-weight: 300; color: var(--ink-muted); }
</style>
</head>
<body>
<main class="stage">
  <section class="card card--front" aria-label="Card front">
    <div class="brand"><span class="brand__dot"></span>Resinworks Hub</div>
  </section>

  <section class="card card--back" aria-label="Card back">
    <div class="brand"><span class="brand__dot"></span>Resinworks Hub</div>

    <p class="address">7-4812 Fernhollow Road,<br>Abbotsford, BC, V3K 8R2.</p>

    <ul class="contacts">
      <li>604-712-3390
        <svg viewBox="0 0 16 16"><path d="M3 2h3l1.5 3.5-2 1.2a8 8 0 0 0 3.8 3.8l1.2-2L14 10v3a1 1 0 0 1-1 1A11 11 0 0 1 2 3a1 1 0 0 1 1-1z"/></svg>
      </li>
      <li>604-947-2164
        <svg viewBox="0 0 16 16"><rect x="4" y="1.5" width="8" height="13" rx="1.5"/><line x1="7" y1="12" x2="9" y2="12"/></svg>
      </li>
      <li>www.resinworkshub.ca
        <svg viewBox="0 0 16 16"><circle cx="8" cy="8" r="6.3"/><ellipse cx="8" cy="8" rx="2.8" ry="6.3"/><line x1="1.7" y1="8" x2="14.3" y2="8"/></svg>
      </li>
      <li>ted@resinworkshub.ca
        <svg viewBox="0 0 16 16"><rect x="1.5" y="3.5" width="13" height="9" rx="1"/><path d="M1.5 4l6.5 5 6.5-5"/></svg>
      </li>
    </ul>

    <div class="person">
      <p class="person__name"><span class="person__first">Ted</span> <span class="person__last">Galloway</span></p>
      <p class="person__title">Founder &amp; CEO</p>
    </div>
  </section>
</main>
</body>
</html>
```